Simple one page Wordpress website

We need a quick turnaround single page wordpress website.
The design needs to be very simple and clean.
We already have some design assets (logos and colours etc) and some draft copy for the page.

We need all the files for us to be able to create a wordpress site. We can do this ourselves and we will host it.

```html
<!DOCTYPE html>
<html lang="en">
<head>
<meta charset="utf-8">
<title>Marlow Vet</title>
<link href="https://fonts.googleapis.com/css2?family=Raleway:wght@700;800&family=Roboto:wght@400;500;700&display=swap" rel="stylesheet">
<style>
:root{
  --blue:#4a86b5;
  --green:#8cb21f;
  --ink:#2f2f2f;
  --body:#555;
  --grey-bg:#f2f2f2;
  --team-bg:#f5f5f5;
  --footer:#2b2b2b;
  --white:#fff;
}
*{box-sizing:border-box;margin:0;padding:0}
html,body{width:1200px;height:4003px;overflow:hidden;background:var(--white)}
body{position:relative;font-family:'Roboto',Arial,sans-serif;color:var(--body)}
.abs{position:absolute}
.heading{font-family:'Raleway',Arial,sans-serif;font-weight:800;text-transform:uppercase;letter-spacing:.5px}

/* header */
.topline{left:0;top:0;width:1200px;height:4px;background:var(--blue)}
.contact-tab{left:622px;top:0;width:463px;height:44px;background:var(--blue);border-radius:0 0 40px 40px;display:flex;align-items:center;justify-content:space-around;color:var(--white);font-size:14px}
.contact-tab span{display:flex;align-items:center;gap:12px}
.ico{width:30px;height:30px;border-radius:50%;background:var(--green);display:inline-flex;align-items:center;justify-content:center}
.brand{left:112px;top:36px;font-weight:500;font-size:44px;color:var(--blue);letter-spacing:2px;line-height:54px}
.nav{top:72px;right:110px;display:flex;gap:28px;font-size:14px;font-weight:500;color:var(--ink)}
.nav .active{color:var(--green)}

/* hero */
.hero-photo{left:0;top:113px;width:1200px;height:650px;background:linear-gradient(90deg,#ecebe8 0%,#e4e3df 45%,#d8d6d1 70%,#cfcac4 100%)}
.hero-edge{left:0;top:620px}
.hero-title{left:112px;top:310px;font-size:40px;line-height:48px;color:var(--ink)}
.hero-sub{left:112px;top:366px;width:420px;font-size:17px;line-height:27px;color:var(--ink);font-weight:500}
.btn{left:112px;top:443px;width:144px;height:48px;border-radius:24px;background:var(--green);color:var(--white);font-size:13px;font-weight:700;display:flex;align-items:center;justify-content:center}
.dots{left:1136px;top:362px;display:flex;flex-direction:column;gap:10px}
.dots i{width:13px;height:13px;border:2px solid var(--blue);border-radius:50%;display:block}
.dots i.on{background:var(--green);border-color:var(--green)}

/* capabilities */
.cap-photo{left:112px;top:741px;width:420px;height:420px;border-radius:50%;background:radial-gradient(circle at 50% 40%,#e8efe9,#a9c6bd 60%,#7a9fa0);border:4px solid var(--blue)}
.cap-title{left:603px;top:848px;font-size:35px;line-height:42px;color:var(--blue)}
.ticks{list-style:none;font-size:14px;line-height:26px;color:var(--body)}
.ticks li{position:relative;padding-left:40px;margin-bottom:10px;text-align:justify}
.ticks li::before{content:"";position:absolute;left:2px;top:6px;width:14px;height:14px;border-radius:50%;background:var(--green)}
.ticks li::after{content:"";position:absolute;left:6px;top:10px;width:4px;height:4px;border-right:2px solid #fff;border-top:2px solid #fff;transform:rotate(45deg)}
.cap-list{left:603px;top:915px;width:486px}

/* turnkey */
.turnkey{left:0;top:1245px;width:1200px;height:454px;background:var(--grey-bg)}
.turnkey-photo{left:600px;top:1245px;width:600px;height:454px;background:linear-gradient(90deg,#f2f2f2 0%,#dfe3e6 30%,#c9cfd4 100%)}
.tk-title{left:112px;top:1296px;width:520px;font-size:25px;line-height:31px;color:var(--blue)}
.tk-text{left:112px;top:1405px;width:484px;font-size:14px;line-height:26px;text-align:justify}
.tk-list{left:112px;top:1495px;width:480px}
.tk-list li{margin-bottom:6px}

/* mission */
.mission-photo{left:0;top:1699px;width:1200px;height:471px;background:linear-gradient(120deg,#b9d3ef 0%,#5f93cc 40%,#2d65a8 75%,#1f4f8a 100%)}
.mission-circle{left:661px;top:1740px;width:390px;height:390px;border-radius:50%;background:rgba(140,178,31,.93);color:var(--white);text-align:center;padding:98px 34px 0}
.mission-circle h2{font-size:33px;line-height:40px;margin-bottom:18px}
.mission-circle p{font-size:14px;line-height:25px}

/* venture */
.jv-title{left:0;top:2258px;width:1200px;text-align:center;font-size:34px;line-height:42px;color:var(--blue)}
.jv-photo{top:2342px;width:470px;height:332px;border-radius:6px;background:linear-gradient(135deg,#eef1f0,#c9d4d6)}
.jv-card{top:2642px;width:420px;height:242px;background:var(--white);border-radius:8px;box-shadow:0 2px 10px rgba(0,0,0,.12);border-bottom:5px solid var(--blue);text-align:center;padding:30px 12px 0}
.jv-card h3{font-size:15px;font-weight:500;color:var(--ink);margin-bottom:18px}
.jv-card p{font-size:13.5px;line-height:26px;color:#666}
.more{margin-top:14px;font-size:13.5px;font-weight:700;color:#a7a400;display:flex;justify-content:center;align-items:center;gap:8px}
.more i{width:12px;height:12px;border-radius:50%;background:var(--green);display:inline-block}

/* team */
.team-bg{left:0;top:2979px;width:1200px;height:660px;background:var(--team-bg)}
.team-title{left:0;top:3040px;width:1200px;text-align:center;font-size:34px;line-height:42px;color:var(--blue)}
.member{top:3117px;width:213px;height:280px;background:var(--white);box-shadow:0 1px 8px rgba(0,0,0,.12);padding:7px;text-align:center}
.member .face{height:218px;background:linear-gradient(180deg,#eeeeee,#d6d6d6)}
.member span{display:block;margin-top:20px;font-size:16px;font-weight:700;color:var(--green)}
.member.active{background:var(--green)}
.member.active span{color:var(--white)}
.pointer{left:226px;top:3396px;width:0;height:0;border-left:11px solid transparent;border-right:11px solid transparent;border-top:14px solid var(--green)}
.team-text{left:129px;top:3445px;width:942px;font-size:14px;line-height:26px;color:#777}

/* footer */
.footer-edge{left:0;top:3580px}
.footer{left:0;top:3660px;width:1200px;height:343px;background:var(--footer)}
.f-brand{left:0;top:3728px;width:1200px;text-align:center;color:var(--white);font-weight:500;font-size:54px;line-height:64px;letter-spacing:3px}
.f-nav{left:0;top:3818px;width:1200px;display:flex;justify-content:center;gap:32px;font-size:18px;font-weight:700;color:var(--white)}
.f-contact{left:0;top:3859px;width:1200px;display:flex;justify-content:center;gap:20px;color:var(--white);font-size:16px;font-weight:500;align-items:center}
.f-social{left:0;top:3897px;width:1200px;display:flex;justify-content:center;gap:10px}
.f-social i{width:32px;height:32px;border-radius:50%;border:2px solid var(--white);display:block}
.f-social i.on{background:var(--green);border-color:var(--green)}
.f-rule{left:112px;top:3946px;width:976px;height:1px;background:#555}
.f-copy{left:0;top:3970px;width:1200px;text-align:center;font-size:13px;color:#ddd}
.f-copy b{color:var(--white)}
</style>
</head>
<body>

<header>
  <div class="abs topline"></div>
  <div class="abs contact-tab">
    <span><i class="ico"><svg width="14" height="14" viewBox="0 0 24 24"><path fill="#fff" d="M6.6 10.8a15 15 0 006.6 6.6l2.2-2.2c.3-.3.7-.4 1-.2 1.1.4 2.3.6 3.6.6.6 0 1 .4 1 1V20c0 .6-.4 1-1 1A17 17 0 013 4c0-.6.4-1 1-1h3.5c.6 0 1 .4 1 1 0 1.3.2 2.5.6 3.6.1.3 0 .7-.2 1z"/></svg></i>+1 (555) 014 2290</span>
    <span><i class="ico"><svg width="14" height="12" viewBox="0 0 24 18"><path fill="#fff" d="M0 0h24v3L12 10 0 3zM0 6l12 7 12-7v12H0z"/></svg></i>hello@marlowvet.com</span>
  </div>
  <div class="abs brand">MARLOW VET</div>
  <nav class="abs nav">
    <span class="active">HOME</span><span>MISSION</span><span>CAPABILITIES</span><span>TURNKEY INITIAL VETERINARY</span><span>VENTURE</span><span>TEAM</span>
  </nav>
</header>

<section>
  <div class="abs hero-photo" role="img" aria-label="Smiling veterinarian in a white coat holding a fluffy cat in a bright clinic"></div>
  <svg class="abs hero-edge" width="1200" height="145" viewBox="0 0 1200 145">
    <path d="M0 145 V70 C400 40 700 160 1200 70 V145 Z" fill="var(--white)"/>
  </svg>
  <h1 class="abs heading hero-title">Welcome to Marlow Vet</h1>
  <p class="abs hero-sub">Marlow Vet is deploying a Software as a Service (SaaS) platform to facilitate the efficient collection</p>
  <div class="abs btn">GET STARTED</div>
  <div class="abs dots"><i></i><i class="on"></i><i></i><i></i><i></i></div>
</section>

<section>
  <div class="abs cap-photo" role="img" aria-label="Two veterinarians in scrubs examining a small white dog"></div>
  <h2 class="abs heading cap-title">Capabilities</h2>
  <ul class="abs ticks cap-list">
    <li>Originally developed for the human market, the core platform has been deployed in the UK and Ireland and has been used to securely process nearly 3 million cases</li>
    <li>The platform has been widely used by leading pharmacies, employers, the public health service and most of the UK’s largest private sector laboratories</li>
  </ul>
</section>

<section>
  <div class="abs turnkey"></div>
  <div class="abs turnkey-photo" role="img" aria-label="Veterinarian and owner smiling over a cat"></div>
  <h2 class="abs heading tk-title">Turnkey Initial Veterinary Deployment – Animal Health and Welfare Pathway</h2>
  <p class="abs tk-text">Marlow Vet is finalising the design of a bespoke platform to facilitate the collection and processing of data and tests for the Animal Health and Welfare Pathway. Key elements include:</p>
  <ul class="abs ticks tk-list">
    <li>Facilitated data collection at the farm by vets</li>
    <li>Secure and efficient processing of test samples by labs</li>
    <li>Digital results reporting</li>
    <li>Invoice support</li>
    <li>Data analysis reporting</li>
  </ul>
</section>

<section>
  <div class="abs mission-photo" role="img" aria-label="Scientist in a blue laboratory examining a blood sample tube"></div>
  <div class="abs mission-circle">
    <h2 class="heading">Mission</h2>
    <p>Marlow Vet is deploying a Software as a Service (SaaS) platform to facilitate the efficient collection, transmission, secure storage and anonymised analysis of data integral to animal diagnostics.</p>
  </div>
</section>

<section>
  <h2 class="abs heading jv-title">Marlow Vet is a Joint Venture</h2>
  <div class="abs jv-photo" style="left:112px" role="img" aria-label="Veterinarians examining a golden dog with a stethoscope"></div>
  <div class="abs jv-photo" style="left:617px" role="img" aria-label="Veterinary nurse with clipboard talking to a man holding a kitten"></div>
  <div class="abs jv-card" style="left:137px">
    <h3>FIELDLINE SOLUTIONS LIMITED (FSL)</h3>
    <p>an innovative veterinary-led, close to market sustainable food research organisation. FSL brings together a team of highly experienced vets representing key opinion leaders within the livestock industry and additional technical</p>
    <div class="more">READ MORE <i></i></div>
  </div>
  <div class="abs jv-card" style="left:642px">
    <h3>CLEARPATH DIAGNOSTICS LIMITED (CPD)</h3>
    <p>is a rapidly growing Software as a Service platform provider in the digital health market. CPD deploys its agile and collaborative software development process working in partnership with its clients, using the skills</p>
    <div class="more">READ MORE <i></i></div>
  </div>
</section>

<section>
  <div class="abs team-bg"></div>
  <h2 class="abs heading team-title">Meet Our Team</h2>
  <svg class="abs" style="left:56px;top:3245px" width="18" height="30" viewBox="0 0 18 30"><path d="M16 2 L3 15 L16 28" stroke="#999" stroke-width="3" fill="none"/></svg>
  <svg class="abs" style="left:1124px;top:3245px" width="18" height="30" viewBox="0 0 18 30"><path d="M2 2 L15 15 L2 28" stroke="#333" stroke-width="3" fill="none"/></svg>
  <div class="abs member active" style="left:129px"><div class="face" role="img" aria-label="Team member portrait"></div><span>ALEX ROWAN</span></div>
  <div class="abs member" style="left:371px"><div class="face" role="img" aria-label="Team member portrait"></div><span>ALEX ROWAN</span></div>
  <div class="abs member" style="left:615px"><div class="face" role="img" aria-label="Team member portrait"></div><span>ALEX ROWAN</span></div>
  <div class="abs member" style="left:858px"><div class="face" role="img" aria-label="Team member portrait"></div><span>ALEX ROWAN</span></div>
  <div class="abs pointer"></div>
  <p class="abs team-text">Ut eget venenatis lectus. Aenean a quam nec quam euismod pellentesque sodales tristiquenunc. Vestibulum vel odio dolor. Nullam ac suscipit quam, in ullamcorper urna. Nam eget turpis innunc ultrices hendrerit. Nullam at urna ut sem euismod porta pharetra nec arcu. Fusce non tellus rhoncus, accumsan risus non, sollicitudin purus. Nunc in magna lectus. Vivamus a posuere eros. Ut vel tellus erat.</p>
</section>

<footer>
  <svg class="abs footer-edge" width="1200" height="82" viewBox="0 0 1200 82">
    <path d="M0 82 V60 C300 -10 700 90 1200 40 V82 Z" fill="var(--footer)"/>
  </svg>
  <div class="abs footer"></div>
  <div class="abs f-brand">MARLOW VET</div>
  <nav class="abs f-nav"><span>HOME</span><span>MISSION</span><span>CAPABILITIES</span><span>TURNKEY INITIAL VETERINARY</span><span>VENTURE</span><span>TEAM</span></nav>
  <div class="abs f-contact">
    <span><svg width="13" height="13" viewBox="0 0 24 24"><path fill="#8cb21f" d="M6.6 10.8a15 15 0 006.6 6.6l2.2-2.2c.3-.3.7-.4 1-.2 1.1.4 2.3.6 3.6.6.6 0 1 .4 1 1V20c0 .6-.4 1-1 1A17 17 0 013 4c0-.6.4-1 1-1h3.5c.6 0 1 .4 1 1 0 1.3.2 2.5.6 3.6.1.3 0 .7-.2 1z"/></svg>&nbsp;&nbsp;+1 (555) 014 2290</span>
    <span>|</span>
    <span><svg width="14" height="11" viewBox="0 0 24 18"><path fill="#8cb21f" d="M0 0h24v3L12 10 0 3zM0 6l12 7 12-7v12H0z"/></svg>&nbsp;&nbsp;hello@marlowvet.com</span>
  </div>
  <div class="abs f-social"><i class="on"></i><i></i><i></i></div>
  <div class="abs f-rule"></div>
  <div class="abs f-copy">© 2022 <b>MARLOW VET</b> &nbsp;/&nbsp; All Rights Reserved</div>
</footer>

</body>
</html>
```